New Web Design needed for our Consulting Business

We have an existing Website that we want a fresh new design for.
www.quorniflow.com.au
Our business is Norvane Tabulo Consulting and we provide services to develop custom spreadsheets to improve business efficiency. We also offer a range of spreadsheets and templates for sale via our website.
Design Deliverables
- Provide a framework for the sites Home Page and each of the key Sub Sections on the site.
- The design deliverable should list the key functions on each framework page so that a developer can interpret those functions for implementation
- The design must include a mobile version for phones and tablet devices or show how the site will appear on those devices.
- We want to project a fresh and professional image with the latest design options for websites
- The existing Logo should be retained and the new design built from that.
What I expect to receive at the end of the Design Project
1) A complete set of design files that can be used by a web developer to construct our new website
2) All image files and colour schemes documented for each page
3) As part of the design the implementation of the functionality listed below is to be clearly documented throughout the site design
4) A word document that provides any key notes or instructions for the web developer to follow for the implementation
Key Sections
Home Page
Tabulo Consulting
Tabulo Software
Free Spreadsheet & Templates
Customer Support
- Blog
- FAQs
- Common Problems
Contact Us
Key Functions
The website must support the following key functions and these should be shown in the design
- Contact Us visible through the site. When a visitor submits a Contact Us form it is stored to a database with a ticket number. Emails are then sent via that Ticket number and stored against that contact on the website for review by our support team. Basically a support ticket tracking system.
- To download a free template or spreadsheet the user must register to the site to receive the download. Those registrations to be kept for later use in email marketing campaigns for the site. Once registered a user can return and "Login" to the site to access more free downloads
- A Blog should be implemented to include interesting articles and information about Quorniflow and Tabulo. This should be a standard Blog design and allow others to comment if they choose to.
- Product Purchase, on the site we offer some products for sale. This currently goes to a 3rd party site for processing. We would like to see this integrated to the site so that the purchase is within our site and also the registration and licence verification. For the design this just needs to show how a Product Purchase would look.
- Site Search will be implemented to provide a site wide search and return results from our site first and then other google results.
- SPAM and Security is a high priority for the site. So the latest protection must be implemented to ensure that the site does not suffer any breach.

```html
<!DOCTYPE html>
<html lang="en">
<head>
<meta charset="utf-8">
<title>Quorniflow — Automating business through Tabulo solutions</title>
<link href="https://fonts.googleapis.com/css2?family=PT+Sans:wght@400;700&display=swap" rel="stylesheet">
<style>
:root{
  --ink:#4a4a4a;
  --brand:#2f44a8;
  --brand-dark:#22318a;
  --brand-light:#5b70d2;
  --green:#3f8a12;
  --topbar:#2b2b2b;
  --rule:#dcdcdc;
  --grey-btn-top:#b9b9b9;
  --grey-btn-bot:#7d7d7d;
  --footer:#333333;
  --footer-dark:#242424;
  --link-red:#b3161b;
}
*{box-sizing:border-box;margin:0;padding:0}
html,body{width:1200px;height:2744px;overflow:hidden}
body{position:relative;background:#fff;font-family:"PT Sans",Arial,sans-serif;color:var(--ink);font-size:13.5px;line-height:22px}
a{color:inherit;text-decoration:none}

/* top utility bar */
.utility-bar{position:absolute;left:0;top:0;width:1200px;height:33px;background:linear-gradient(#3a3a3a,var(--topbar))}
.utility-links{position:absolute;right:100px;top:0;height:33px;display:flex;align-items:center;color:#e6e6e6;font-size:13px}
.utility-links .sep{margin:0 16px;color:#888}

/* header */
.site-header{position:absolute;left:0;top:33px;width:1200px;height:155px;background:linear-gradient(#f6f6f6,#ffffff 60%,#f1f1f1)}
.brand{position:absolute;left:104px;top:28px;display:flex;align-items:center;gap:10px}
.brand-dot{width:54px;height:54px;border-radius:50%;background:var(--brand)}
.brand-name{font-weight:700;font-size:27px;color:var(--brand-dark)}
.tagline{position:absolute;left:249px;top:72px;font-weight:700;font-size:25px;line-height:32px;color:#5278d0}
.call-us{position:absolute;right:102px;top:35px;font-size:18px;color:#555;font-weight:700}
.call-us strong{color:var(--brand);font-size:22px}
.search-box{position:absolute;left:832px;top:88px;width:266px;height:34px;border:1px solid #d4d4d4;background:#fff;font-size:13px;color:#999;padding:6px 12px}
.search-btn{position:absolute;right:4px;top:4px;width:24px;height:24px;background:linear-gradient(#a8a8a8,#777);border-radius:2px}

/* main nav */
.main-nav{position:absolute;left:0;top:188px;width:1200px;height:52px;background:linear-gradient(var(--brand-light),var(--brand) 55%,var(--brand-dark))}
.main-nav ul{list-style:none;position:absolute;left:100px;top:0;display:flex;height:52px}
.main-nav li{height:52px;display:flex;align-items:center;padding:0 26px;color:#fff;font-size:14.5px;border-right:1px solid rgba(255,255,255,.18)}
.main-nav li.current{background:linear-gradient(#7f91df,#4f63c3);width:107px;justify-content:center;padding:0}

/* hero */
.hero{position:absolute;left:100px;top:263px;width:1000px;height:346px;background:#fff;box-shadow:0 8px 10px -6px rgba(0,0,0,.25);border:1px solid #eee}
.hero-visual{position:absolute;left:8px;top:11px;width:728px;height:322px;background:linear-gradient(90deg,#2c3c68 0%,#6f84a9 35%,#d8dde6 62%,#f1f1f1 100%)}
.hero-headline{position:absolute;left:450px;top:90px;width:256px;text-align:right;font-weight:700;font-size:24px;line-height:30px;color:#333}
.hero-sub{position:absolute;left:450px;top:125px;width:256px;text-align:right;font-size:14px;color:#333}
.hero-cta{position:absolute;left:586px;top:166px;width:120px;height:38px;border-radius:4px;background:linear-gradient(var(--grey-btn-top),var(--grey-btn-bot));color:#fff;font-weight:700;font-size:16px;display:flex;align-items:center;justify-content:center}
.hero-dots{position:absolute;left:618px;top:291px;display:flex;gap:9px}
.hero-dots i{width:13px;height:13px;border-radius:50%;background:#bbb;display:block}
.hero-dots i:first-child{background:#888}
.product-menu{position:absolute;left:767px;top:26px}
.product-menu h2{font-size:19px;color:var(--brand);font-weight:700;margin-bottom:6px}
.product-menu li{list-style:none;font-size:14.5px;line-height:31px;color:#333}
.product-menu li::before{content:"» ";color:#333}

/* main column: blocks placed on the page grid */
.content-main{position:absolute;left:104px;top:0;width:651px;height:2588px}
.content-main > *{position:absolute;left:0;width:651px}
.intro{top:658px}
.intro-icon{float:left;width:76px;height:79px;margin:2px 19px 4px 0;background:linear-gradient(135deg,#eef1f6,#b8c4d6);border:1px solid #c9c9c9}
.section-title{font-size:21px;font-weight:700;color:var(--brand);line-height:26px}
.intro-lead{line-height:22px}
.intro-body{top:781px;line-height:33px}
.callout{top:962px;color:var(--green)}
.btn{display:flex;align-items:center;justify-content:center;height:38px;border-radius:3px;background:linear-gradient(var(--grey-btn-top),var(--grey-btn-bot));color:#fff;font-weight:700;font-size:16px;letter-spacing:.2px}
.content-main > .btn-quote{top:995px;left:183px;width:286px}
.plus{top:1044px;line-height:29.3px}
.divider{top:1161px;border:0;border-top:1px solid var(--rule)}
.examples-title{top:1188px;font-size:23px;line-height:30px;font-weight:700;color:var(--brand)}
.service-head{font-size:16px;line-height:22px;font-weight:400;color:var(--green)}
.service-text{line-height:29.3px}
.video-link{color:var(--brand-dark)}
.content-main > .btn-consultant{top:2427px;left:152px;width:348px}
.closing{top:2483px;line-height:27.5px}
.inline-link{color:var(--brand)}

/* sidebar: blocks placed on the page grid */
.content-side{position:absolute;left:807px;top:0;width:291px;height:2588px}
.content-side > *{position:absolute;left:0;width:291px}
.side-title{font-size:21px;font-weight:700;color:var(--brand);line-height:26px}
.video-frame{height:182px;background:linear-gradient(160deg,#3a3a3a,#7a2a24 55%,#c9c9c9)}
.video-frame svg{position:absolute;left:117px;top:62px}
.video-bar{position:absolute;left:0;bottom:0;width:100%;height:12px;background:#111}
.view-all{color:var(--link-red)}
.side-rule{border:0;border-top:1px solid var(--rule)}
.side-nav{list-style:none}
.side-nav li{font-size:14.5px;line-height:37.7px;color:#333}
.side-nav li::before,.side-links li::before{content:"» "}
.teaser{display:flex;gap:14px;align-items:flex-start}
.teaser-art{flex:0 0 76px;height:82px;margin-top:3px;background:linear-gradient(135deg,#d9eed3,#5aa43c)}
.teaser-art.pen{background:linear-gradient(135deg,#eef2f7,#9aa9be)}
.teaser-art.mail{background:linear-gradient(135deg,#f4e7c9,#c9a66a)}
.teaser h2{font-size:21px;font-weight:700;color:var(--brand);line-height:26px;margin-bottom:3px}
.teaser p{font-size:12.5px;line-height:19px;color:#444}
.teaser .more{color:var(--brand)}
.side-links{list-style:none}
.side-links li{font-size:13.5px;line-height:27.5px;color:var(--green)}
.content-side > .btn-subscribe{width:276px}
.signup-note{font-size:12.5px;line-height:19px;color:#444}

/* footer */
.site-footer{position:absolute;left:0;top:2590px;width:1200px;height:154px;background:linear-gradient(var(--footer-dark),var(--footer) 30%)}
.footer-nav{position:absolute;left:0;top:18px;width:1200px;display:flex;justify-content:center;color:#ddd;font-size:13.5px}
.footer-nav .sep{margin:0 11px;color:#888}
.footer-rule{position:absolute;left:100px;top:62px;width:998px;border-top:1px solid #4a4a4a}
.copyright{position:absolute;left:100px;top:82px;color:#bbb;font-size:12.5px}
.legal{position:absolute;left:100px;top:114px;color:#bbb;font-size:12.5px}
.legal span{margin:0 8px;color:#777}
.social{position:absolute;left:925px;top:99px;display:flex;gap:19px}
.social i{display:block;width:33px;height:33px;border-radius:50%;background:#4d5f9b}
.social i:nth-child(2){background:#4b8fc5}
.social i:nth-child(3){background:#b23a2f}
.social i:nth-child(4){background:#cf7a25}
</style>
</head>
<body>

<div class="utility-bar">
  <nav class="utility-links"><a href="#">Contact us</a><span class="sep">|</span><a href="#">Blog</a><span class="sep">|</span><a href="#">Members Log in</a></nav>
</div>

<header class="site-header">
  <div class="brand"><span class="brand-dot"></span><span class="brand-name">Quorniflow</span></div>
  <div class="tagline">Automating business<br>through Tabulo solutions</div>
  <div class="call-us">Call us : <strong>+61 (7) 5550 0148</strong></div>
  <div class="search-box">Search<span class="search-btn"></span></div>
</header>

<nav class="main-nav">
  <ul>
    <li class="current">Home</li>
    <li>Tabulo Consulting</li>
    <li>Tabulo Software</li>
    <li>Free Spreadsheets &amp; Templates</li>
    <li>Customer Support</li>
    <li>Contact Us</li>
  </ul>
</nav>

<section class="hero">
  <div class="hero-visual" role="img" aria-label="Photo of a business team gathered around a laptop"></div>
  <div class="hero-headline">Namut imperdiet sem</div>
  <div class="hero-sub">Class aptent taciti sociosquad</div>
  <a class="hero-cta" href="#">CONTACT US</a>
  <div class="hero-dots"><i></i><i></i><i></i><i></i></div>
  <div class="product-menu">
    <h2>Tabulo Software Products</h2>
    <ul>
      <li>Quote Generator</li>
      <li>Stock Ledger Watch Pro</li>
      <li>Task Roster Pro</li>
      <li>Job Tracker</li>
      <li>Your Business Dashboard</li>
      <li>Invoice Generator</li>
      <li>Notice Relay</li>
      <li>Macro Shroud</li>
    </ul>
  </div>
</section>

<main class="content-main">
  <div class="intro">
    <div class="intro-icon" role="img" aria-label="Spreadsheet tools icon"></div>
    <h1 class="section-title">Tabulo Consulting</h1>
    <p class="intro-lead">At Quorniflow we specialise in Tabulo Application development. Our Tabulo Consultants have years of experience in developing solutions to improve your business. We know Norvane Tabulo inside-out and back-to-front.</p>
  </div>
  <p class="intro-body">&nbsp;We work for clients in many different industries, providing Tabulo Help that can be as simple as building an Tabulo Formula or as complex as developing a complete custom Tabulo Application. We are so confident in our service being able to improve your existing use of Tabulo that we offer a "Money-Back" guarantee to our clients. If during a project with Quorniflow we are unable to improve or enhance your current use of Tabulo within your business then you pay nothing for our service. This guarantee is offered as part of our Tabulo Consulting service.</p>
  <p class="callout">"Its easy to use our Tabulo Consulting Service... simply click on the link below to talk via email or phone today"</p>
  <a class="btn btn-quote" href="#">REQUEST A FREE QUOTE TODAY</a>
  <p class="plus">Plus... did you know that our Tabulo Consultants provide a no-obligation FREE of charge quotation service for you. That means you don't even have to think about making a decision. Just simply Request a FREE quote right now and start discovering how you can use our Tabulo Consulting Service to help your business grow.</p>
  <hr class="divider">
  <h2 class="examples-title">Examples of our Tabulo Consulting Services</h2>

  <h3 class="service-head" style="top:1244px">Custom Spreadsheets</h3>
  <p class="service-text" style="top:1267px">Successful businesses use the power of well developed Custom Spreadsheets to save time and enhance their business process. Our Spreadsheet Development team offer affordable, simple to use, and well thought-out Spreadsheet Solutions specific for your business.</p>

  <h3 class="service-head" style="top:1370px">Macro Programming</h3>
  <p class="service-text" style="top:1395px">As part of our Tabulo Consulting service we provide Macro Programming. Some examples are the development of database macros, time saving macros, automatic chart creation macros and complete macro driven applications. We also fix existing macros that may have been developed by someone that has since left your organisation.</p>

  <h3 class="service-head" style="top:1527px">Statistical and Financial Calculations</h3>
  <p class="service-text" style="top:1553px;line-height:27.5px">Is your business reliant on statistics and calculations for vital information and decisions ? The Quorniflow development team can improve your existing process through the use of Norvane Tabulo®. Be assured that your analysis and resulting calculations are accurate.</p>
  <p class="service-text" style="top:1641px;line-height:27.5px">If you already use Norvane Tabulo® Click here to provide to us with some sample Spreadsheets and Workbooks for us to analyse for you. Its FREE......Thats right we will provide you with a no-obligation FREE of charge quotation service.</p>

  <h3 class="service-head" style="top:1745px">Customised Tabulo Reporting</h3>
  <p class="service-text" style="top:1770px;line-height:29px">Make quick and informed decisions with visually presented critical data in summary form! Turn your existing data into a rich set of functional reports, through the use of interactive Tabulo Pivot Charts and Tables to produce specific reports crucial to making key decisions.</p>
  <p class="service-text" style="top:1862px;line-height:27px">Be amazed at how our Tabulo Consultants can help you take advantage of Tabulo Dashboard Reporting to see your most important data in a single page of reports, ready to compare at a glance. Gain new levels of insight and critical understanding of you business! Many businesses have databases of information that are not effectively or efficiently used ? For example staff may be extracting and converting data from existing accounting and sales systems into reports for management on a regular basis. Click here to send us your ideas or sample reports and we will work together to produce real proposals to improve your business.<br><span class="video-link">View this Video : &nbsp;http://vidlink.example/qf7Tb2</span></p>

  <h3 class="service-head" style="top:2080px">Templates for Business Use</h3>
  <p class="service-text" style="top:2107px;line-height:31px">Improve staff efficiency through automated and consistent Spreadsheet Templates. If your business already uses Norvane Tabulo® for day to day operations there may be a need to develop automated templates to ensure consistent use of functions and procedures. For example your sales consultants may currently produce estimates of effort and cost manually or through interaction with a series of systems. This can be achieved through the use of a single template that is consistently used throughout your sales team.</p>

  <h3 class="service-head" style="top:2268px">Quotation and Invoicing - Keeping it SIMPLE!</h3>
  <p class="service-text" style="top:2295px;line-height:30px">Some accounting systems can cost hundreds of dollars offering features and functions that you may never need or use. Other systems require that you sign up to costly long term monthly agreements. Our Tabulo Consulting team have developed simple easy to use custom Quotation and Invoice systems keeping the focus on their purpose to create and manage quotes and invoices.</p>

  <a class="btn btn-consultant" href="#">CONTACT AN TABULO CONSULTANT NOW</a>
  <p class="closing">Our Development Team pride themselves on satisfying our clients requirements with the highest level of service. Our professional approach, strong communication and attention to detail are consistently highlighted in feedback from our customers. <span class="inline-link">Click Here</span> to hear what our customers have to say about us.</p>
</main>

<aside class="content-side">
  <h2 class="side-title" style="top:656px">Tabulo Chart Creation Macro Demo</h2>
  <div class="video-frame" style="top:722px" role="img" aria-label="Video still of a rising share price chart">
    <svg width="56" height="56" viewBox="0 0 56 56"><circle cx="28" cy="28" r="25" fill="rgba(0,0,0,.35)" stroke="#fff" stroke-width="3"/><path d="M22 16 L40 28 L22 40 Z" fill="#fff"/></svg>
    <div class="video-bar"></div>
  </div>
  <a class="view-all" href="#" style="top:914px">View All Videos</a>
  <hr class="side-rule" style="top:962px">

  <h2 class="side-title" style="top:987px">Tabulo Consulting</h2>
  <ul class="side-nav" style="top:1020px">
    <li>Consulting Overview</li>
    <li>Macro Programming</li>
    <li>Spreadsheet Development</li>
    <li>Tabulo Dashboard Reporting</li>
    <li>Customer Testimonials</li>
    <li>Programming &amp; Consulting Rates</li>
    <li>About Us</li>
    <li>Newsletter</li>
    <li>Partner Organisations</li>
  </ul>
  <hr class="side-rule" style="top:1379px">

  <div class="teaser" style="top:1414px">
    <div class="teaser-art" role="img" aria-label="Spreadsheet document icon"></div>
    <div><h2>Tabulo Software</h2><p>Our product offerings are based on Norvane Tabulo® and have been developed... <span class="more">More</span></p></div>
  </div>
  <ul class="side-links" style="top:1524px">
    <li>Invoice Generator</li>
    <li>Your Business Dashboard - onl</li>
    <li>Task Roster Pro</li>
  </ul>
  <hr class="side-rule" style="top:1627px">

  <div class="teaser" style="top:1662px">
    <div class="teaser-art pen" role="img" aria-label="Pen and notepad icon"></div>
    <div><h2>Testimonials</h2><p>"I found the Quorniflow team to be very professional, courteous and knowledgeable,... <span class="more">More</span></p></div>
  </div>
  <ul class="side-links" style="top:1771px">
    <li>Terrabend Surveys</li>
    <li>Lidmore Homewares</li>
    <li>Vantrel Online</li>
  </ul>
  <hr class="side-rule" style="top:1884px">

  <div class="teaser" style="top:1908px">
    <div class="teaser-art mail" role="img" aria-label="Envelope icon"></div>
    <div><h2>Newsletter Signup</h2><p>The Quorniflow Newsletter is a vital source of information and advice on using Norvane® Tabulo</p></div>
  </div>
  <a class="btn btn-subscribe" href="#" style="top:2019px">SUBSCRIBE NOW</a>
  <p class="signup-note" style="top:2079px">If you are not yet a subscriber then click on this link to register as a member to our website and receive our monthly newsletter</p>
</aside>

<footer class="site-footer">
  <nav class="footer-nav">
    <a href="#">Home</a><span class="sep">|</span><a href="#">Tabulo Consulting</a><span class="sep">|</span><a href="#">Tabulo Software</a><span class="sep">|</span><a href="#">Free Spreadsheets &amp; Templates</a><span class="sep">|</span><a href="#">Customer Support</a><span class="sep">|</span><a href="#">Contact Us</a>
  </nav>
  <div class="footer-rule"></div>
  <div class="copyright">Copyright © Quorniflow. &nbsp;&nbsp;All rights reserved</div>
  <div class="legal">Privacy Policy<span>|</span>Terms and conditions</div>
  <div class="social" aria-label="Social links"><i></i><i></i><i></i><i></i></div>
</footer>

</body>
</html>
```